Forensic Document Examiner, looking for contemporary update to my stationery design.

Looking for professional, classy logo design for stationery and business cards. My current stationery and business card is attached.I believe a logo image makes a header section interesting, so an intriguing design of a pen, feathered pen, microscope, magnifying glass, etc., would be appropriate. I have been in the business for over 30 years. I leave ideas to the imagination of the designer.My work involves mainly, the comparison of signatures and handwriting. I also resolve alterations, obliterations, and work as shown on my website: www.documentexaminer.infoThe image produced will be printed on quality white stationery and envelopes. The stationery will be photocopied by my clients, so the images should be reproducible. The business cards may be designed in other than white.

Target Market(s)

Attorneys

Font styles to use
Sans Serif

Colors

Designer to choose colors to be used in the design.

Requirements
Must have
• Image suitable for white stationery and photocopying.
• Classy logo and image; no casual fonts.
Nice to have
• Intriguing, contemporary design incorporating a relevant logo to my work.

```html
<!DOCTYPE html>
<html lang="en">
<head>
<meta charset="utf-8">
<title>Nora B. Hale Stationery</title>
<link href="https://fonts.googleapis.com/css2?family=Didact+Gothic&family=Open+Sans:wght@400;600&display=swap" rel="stylesheet">
<style>
  :root {
    --backdrop: #838383;
    --paper: #f7f7f7;
    --brand: #2e2aa0;
    --ink: #4a4a4a;
    --ink-soft: #5a5a5a;
    --flap-line: #dcdcdc;
  }
  * { margin: 0; padding: 0; box-sizing: border-box; }
  html, body { width: 1200px; height: 877px; overflow: hidden; background: var(--backdrop); }
  .canvas { position: relative; width: 1200px; height: 877px; }
  .sheet { position: absolute; background: var(--paper); }

  .letterhead { left: 59px; top: 66px; width: 527px; height: 742px; }
  .brand { position: absolute; display: flex; align-items: center; gap: 6px;
    font-family: "Open Sans", sans-serif; font-weight: 600; color: var(--brand); }
  .brand-dot { width: 14px; height: 14px; border-radius: 50%; background: var(--brand); flex: none; }
  .letterhead .brand { left: 45px; top: 42px; font-size: 20px; }

  .contact { position: absolute; right: 42px; top: 43px; list-style: none;
    font-family: "Open Sans", sans-serif; font-size: 8px; line-height: 10.7px;
    color: var(--ink); text-align: right; }
  .contact li { display: flex; justify-content: flex-end; align-items: center; gap: 3px; }
  .contact svg { width: 7px; height: 7px; fill: var(--brand); }

  .letter { position: absolute; left: 45px; top: 208px; width: 438px;
    font-family: "Didact Gothic", sans-serif; color: var(--ink-soft); }
  .salutation { font-size: 13.5px; margin-bottom: 22px; }
  .letter p.body { font-size: 7.5px; line-height: 11.4px; margin-bottom: 11.4px; text-align: justify; }
  .closing { font-size: 7.5px; margin-top: 21px; }
  .signature { width: 62px; height: 24px; margin-top: 8px; background: #e6e6e8; }

  .envelope-back { left: 620px; top: 293px; width: 530px; height: 239px; }
  .flap { position: absolute; left: 0; top: 0; }
  .envelope-back .brand-dot { position: absolute; left: 258px; top: 28px; width: 16px; height: 16px; }

  .envelope-front { left: 620px; top: 566px; width: 532px; height: 242px; }
  .envelope-front .brand { left: 32px; top: 30px; font-size: 20px; }
  .return-address { position: absolute; left: 39px; top: 72px;
    font-family: "Open Sans", sans-serif; font-size: 8px; color: var(--ink); }
</style>
</head>
<body>
<main class="canvas">
  <section class="sheet letterhead">
    <div class="brand"><span class="brand-dot"></span>Nora B. Hale</div>
    <ul class="contact">
      <li><svg viewBox="0 0 10 10"><path d="M2 0l2 2-1 2c1 1 2 2 3 3l2-1 2 2-2 2C4 10 0 6 0 2z"/></svg>(888) 555-0147</li>
      <li><svg viewBox="0 0 10 10"><path d="M0 2h10v6H0z"/></svg>nhale@quillmarkreview.info</li>
      <li><svg viewBox="0 0 10 10"><circle cx="5" cy="5" r="5"/></svg>www.quillmarkreview.info</li>
      <li><svg viewBox="0 0 10 10"><path d="M5 0a4 4 0 0 1 4 4c0 3-4 6-4 6S1 7 1 4a4 4 0 0 1 4-4z"/></svg>P.O.Box 2140, Salem, OR 97301</li>
    </ul>
    <article class="letter">
      <p class="salutation">Dear Mr. Carter,</p>
      <p class="body">Lorem ipsum dolor sit amet, consectetur adipiscing elit. Donec orci purus, luctus vitae dignissim eu, iaculis sed purus. Vivamus faucibus, ipsum nec aliquet viverra, leo mauris condimentum ligula, sit amet sagittis enim ligula quis arcu. Nam egestas tortor id nisi porttitor mattis. In tortor ante, ultricies in suscipit a, tempus non massa. Vivamus et auctor mi. Fusce vel massa nulla. Phasellus nec eros mauris, et scelerisque orci.</p>
      <p class="body">Donec malesuada orci vitae nulla accumsan porta a id massa. Quisque accumsan iaculis magna sit amet fringilla. Maecenas consequat, magna eget tincidunt semper, odio nibh rutrum mi, id feugiat ante nisi eu risus. Vestibulum nunc orci, rhoncus a placerat in, ultricies in mi. Cras mattis varius eros, vel fringilla nisi suscipit eget. Quisque scelerisque sagittis nulla at porttitor.</p>
      <p class="body">Sed id augue vitae urna euismod commodo aliquet a quam. Pellentesque arcu velit, cursus et malesuada ut, consequat et diam. Nullam erat sem, rhoncus id ullamcorper vitae, rhoncus et arcu. In ultricies ultricies nulla, ut rutrum nisi iaculis at. Donec eu magna a metus ornare faucibus. Fusce aliquet faucibus ultricies. Morbi semper, est id tincidunt gravida, sem arcu adipiscing lacus, ac bibendum nulla leo eu purus. Quisque nec diam sed risus consectetur accumsan quis quis nibh. Vestibulum id purus lorem.</p>
      <p class="body">It is a long established fact that a reader will be distracted by the readable content of a page when looking at its layout. The point of using Lorem Ipsum is that it has a more-or-less normal distribution of letters, as opposed to using 'Content here, content here', making it look like readable English. Many desktop publishing packages</p>
      <p class="closing">Sincerely,</p>
      <div class="signature" role="img" aria-label="Handwritten signature"></div>
    </article>
  </section>

  <section class="sheet envelope-back">
    <svg class="flap" width="530" height="80" viewBox="0 0 530 80">
      <path d="M12 0 Q12 60 40 70 L490 70 Q518 60 518 0" fill="none" stroke="var(--flap-line)" stroke-width="2"/>
    </svg>
    <span class="brand-dot"></span>
  </section>

  <section class="sheet envelope-front">
    <div class="brand"><span class="brand-dot"></span>Nora B. Hale</div>
    <p class="return-address">P.O.Box 2140, Salem, OR 97301</p>
  </section>
</main>
</body>
</html>
```